New Webpage for High Class Expert Witness Services Company

We are looking for a minimalist design for a webpage that just has our logo and an entry form offer to connect with one of our Liaisons.
The entry form should just ask for Name, Email, Contact Info and Description of Project.

Company Name is: The Marlowe Crest Advisory Services

Number of Pages Required

1 page

```html
<!DOCTYPE html>
<html lang="en">
<head>
<meta charset="utf-8">
<title>Marlowe Crest Advisory Services</title>
<link href="https://fonts.googleapis.com/css2?family=Cinzel:wght@400;600&family=Manrope:wght@400&family=Roboto:wght@400;500&display=swap" rel="stylesheet">
<style>
  :root {
    --bg-dark: #141414;
    --bg-mid: #2a2a2a;
    --bg-light: #4a4a4a;
    --panel: rgba(8, 8, 8, 0.92);
    --text-main: #ffffff;
    --text-soft: #c9c9c9;
    --text-muted: #9a9a9a;
    --field-border: #bdbdbd;
    --rule: #5a5a5a;
    --button-from: #e4e4e6;
    --button-to: #9a9a9d;
    --button-text: #111111;
  }
  * { box-sizing: border-box; margin: 0; padding: 0; }
  html, body { width: 1200px; height: 742px; overflow: hidden; }
  body {
    position: relative;
    background: var(--bg-dark);
    color: var(--text-main);
    font-family: "Manrope", sans-serif;
  }
  .hero-photo {
    position: absolute; inset: 0;
    background:
      radial-gradient(ellipse 420px 380px at 680px 300px, rgba(110,110,110,0.35), transparent 70%),
      radial-gradient(ellipse 360px 420px at 1100px 420px, rgba(120,120,120,0.3), transparent 70%),
      linear-gradient(90deg, var(--bg-dark) 0%, #1c1c1c 35%, var(--bg-mid) 60%, var(--bg-light) 100%);
  }
  .brand {
    position: absolute; left: 114px; top: 44px;
    display: flex; align-items: center; gap: 14px;
  }
  .brand-mark { width: 40px; height: 40px; background: #d0d0d0; }
  .brand-name {
    font-family: "Cinzel", serif; font-weight: 400;
    font-size: 24px; line-height: 1.1; letter-spacing: 1.5px;
    color: #d6d6d6; width: 300px;
  }
  .eyebrow {
    position: absolute; left: 111px; top: 219px;
    font-family: "Cinzel", serif; font-size: 15.5px; letter-spacing: 1.6px;
    color: var(--text-muted);
  }
  .headline {
    position: absolute; left: 114px; top: 260px;
    border-left: 1px solid var(--rule);
    padding-left: 21px;
    font-family: "Cinzel", serif; font-weight: 400;
    font-size: 50px; line-height: 50px; letter-spacing: 2px;
    color: var(--text-main);
  }
  .intro {
    position: absolute; left: 114px; top: 426px; width: 480px;
    font-size: 14px; line-height: 27px; color: var(--text-soft);
  }
  .contact-panel {
    position: absolute; left: 714px; top: 123px; width: 381px; height: 439px;
    background: var(--panel);
    padding: 36px 48px 0 48px;
  }
  .contact-title {
    display: flex; align-items: center; gap: 12px;
    font-family: "Cinzel", serif; font-size: 24px; letter-spacing: 0.5px;
    margin-bottom: 20px;
  }
  .contact-title .title-mark { width: 18px; height: 18px; background: #d0d0d0; }
  .field {
    display: block; width: 294px; height: 42px;
    background: transparent; border: 1px solid var(--field-border); border-radius: 2px;
    color: var(--text-main);
    font-family: "Roboto", sans-serif; font-weight: 500; font-size: 13px;
    padding: 0 17px; margin-bottom: 12px;
  }
  .field::placeholder { color: var(--text-main); opacity: 1; }
  textarea.field { height: 89px; padding-top: 11px; resize: none; margin-bottom: 13px; }
  .submit {
    display: block; width: 298px; height: 44px; border: 0; border-radius: 2px;
    background: linear-gradient(110deg, var(--button-from) 0%, #d3d3d6 45%, var(--button-to) 75%, #b0b0b3 100%);
    color: var(--button-text);
    font-family: "Cinzel", serif; font-weight: 600; font-size: 15px; letter-spacing: 0.6px;
  }
  .site-footer {
    position: absolute; left: 0; right: 0; top: 680px; bottom: 0;
    border-top: 1px solid var(--rule);
  }
  .copyright {
    position: absolute; left: 142px; top: 20px;
    font-family: "Roboto", sans-serif; font-size: 12.5px; color: var(--text-muted);
  }
</style>
</head>
<body>
  <div class="hero-photo" role="img" aria-label="Monochrome photo of a doctor in a white coat holding a stethoscope"></div>

  <header class="brand">
    <span class="brand-mark"></span>
    <span class="brand-name">Marlowe Crest Advisory Services</span>
  </header>

  <p class="eyebrow">MARLOWE CREST ADVISORY SERVICES</p>
  <h1 class="headline">SEAMLESS<br>MEDICAL EXPERT<br>INTEGRATION</h1>
  <p class="intro">Lorem ipsum dolor sit amet, consectetur adipiscing elit, sed do eiusmod tempor incididunt ut labore et dolore magna aliqua.</p>

  <form class="contact-panel">
    <h2 class="contact-title"><span class="title-mark"></span>CONNECT WITH US</h2>
    <input class="field" type="text" placeholder="Name*">
    <input class="field" type="email" placeholder="Email*">
    <input class="field" type="tel" placeholder="Phone number*">
    <textarea class="field" placeholder="Description of Project"></textarea>
    <button class="submit" type="button">SUBMIT</button>
  </form>

  <footer class="site-footer">
    <p class="copyright">© 2026 Marlowe Crest Advisory Services. All Rights Reserved</p>
  </footer>
</body>
</html>
```